4th Generation Family Business Needs a New Card Design!

We are a family owned 4th Generation company. We are based in the Sydney, Australia area and we are desperately in need of a more modern and classy card. We are monumental masons who design, supply & erect lasting memorials throughout cemeteries in Sydney. Our customers are normally in a period of grieving. I have attached logo files that will need to be implemented on the card. Company was established 1935. Australian Owned and Operated. Card needs to be designed to PIXO.com specification.

Target Market(s)

Our target market is based upon people that a grieving for family members that have passed away. We also deal with alot of companies that own and operate cemeteries.

Industry/Entity Type

Business

Contact Information for Business Card

Simon Harcourt, Operations Manager, 0417293086, simon@harcourtmemorials.com.au
Lewis Harcourt, Director, 0491630572, lewis@harcourtmemorials.com.au
Phone # 02 9561 3048
Website: www.harcourtmemorials.com.au
Address: Suite 17, 8 Palfrey Lane, West Carlow, Sydney NSW 2156

Font styles to use
Serif
Decorative
Script

Requirements
Must have
• Would like to see the logo nicely implemented with a modern design. Embossed lettering would be a nice additive.

```html
<!DOCTYPE html>
<html lang="en">
<head>
<meta charset="utf-8">
<title>Harcourt Memorials – Business Card</title>
<link rel="stylesheet" href="https://fonts.googleapis.com/css2?family=Cinzel:wght@400;600&family=Open+Sans:wght@300;400&display=swap">
<style>
  :root {
    --bg: #e6e6e6;
    --card: #ffffff;
    --ink: #231f20;
    --gold: #f2c12e;
    --grey-text: #5a5a5a;
    --panel: #f4f4f4;
    --rule: #d6d6d6;
  }
  * { box-sizing: border-box; margin: 0; padding: 0; }
  html, body {
    width: 1200px; height: 950px; overflow: hidden;
    background: var(--bg);
  }
  .card {
    position: absolute;
    left: 250px;
    width: 700px; height: 400px;
    background: var(--card);
    box-shadow: 0 6px 18px rgba(0,0,0,0.18);
    overflow: hidden;
  }
  .card--front { top: 50px; }
  .card--back { top: 500px; }

  /* Front */
  .brand {
    position: absolute; inset: 0;
    display: flex; align-items: center; justify-content: center;
  }
  .brand__name {
    font-family: 'Cinzel', serif;
    font-weight: 600;
    font-size: 40px;
    letter-spacing: 2px;
    color: var(--ink);
  }

  /* Back */
  .contact-panel {
    position: absolute; top: 0; right: 0;
    width: 320px; height: 100%;
    background: linear-gradient(90deg, #fafafa, var(--panel));
    border-left: 1px solid var(--rule);
  }
  .person {
    position: absolute; left: 0; top: 0;
    width: 380px; height: 100%;
    display: flex; flex-direction: column; justify-content: center; align-items: center;
    padding-bottom: 10px;
  }
  .person__name {
    font-family: 'Cinzel', serif;
    font-size: 30px;
    font-weight: 400;
    color: var(--ink);
    letter-spacing: 1px;
  }
  .person__title {
    font-family: 'Cinzel', serif;
    font-size: 17px;
    color: var(--gold);
    letter-spacing: 2px;
    margin-top: 2px;
  }
  .details {
    position: absolute; left: 405px; top: 88px;
    font-family: 'Open Sans', sans-serif;
    font-weight: 300;
    color: var(--grey-text);
    font-size: 16px;
    line-height: 1.45;
  }
  .details__address { margin-bottom: 14px; }
  .details__list { list-style: none; }
  .details__item { display: flex; align-items: center; gap: 10px; }
  .details__item svg { width: 15px; height: 15px; flex: none; }

  .footer-band { position: absolute; bottom: 0; height: 14px; }
  .footer-band--left { left: 0; width: 300px; background: var(--gold); }
  .footer-band--mid { left: 300px; width: 140px; height: 20px; background: var(--ink); }
  .footer-band--right { left: 440px; right: 0; background: var(--gold); }
</style>
</head>
<body>

<section class="card card--front" aria-label="Card front">
  <div class="brand">
    <span class="brand__name">HARCOURT MEMORIALS</span>
  </div>
</section>

<section class="card card--back" aria-label="Card back">
  <div class="contact-panel"></div>

  <div class="person">
    <h1 class="person__name">SIMON HARCOURT</h1>
    <p class="person__title">OPERATIONS MANAGER</p>
  </div>

  <div class="details">
    <p class="details__address">Suite 17, 8 Palfrey Lane<br>West Carlow, Sydney NSW 2156</p>
    <ul class="details__list">
      <li class="details__item">
        <svg viewBox="0 0 16 16" aria-hidden="true"><path fill="#231f20" d="M3.5 1l2.5 3-1.5 1.5c.8 2 2.5 3.7 4.5 4.5L10.5 8.5l3 2.5-1.5 3C7 14 2 9 2 2.5z"/></svg>
        <span>02 9561 3048</span>
      </li>
      <li class="details__item">
        <svg viewBox="0 0 16 16" aria-hidden="true"><rect x="4" y="1" width="8" height="14" rx="1.5" fill="none" stroke="#231f20" stroke-width="1.5"/><circle cx="8" cy="12.5" r="0.9" fill="#231f20"/></svg>
        <span>0417293086</span>
      </li>
      <li class="details__item">
        <svg viewBox="0 0 16 16" aria-hidden="true"><rect x="1" y="3" width="14" height="10" fill="#231f20"/><path d="M1.5 3.5L8 9l6.5-5.5" fill="none" stroke="#fff" stroke-width="1.2"/></svg>
        <span>simon@harcourtmemorials.com.au</span>
      </li>
      <li class="details__item">
        <svg viewBox="0 0 16 16" aria-hidden="true"><circle cx="8" cy="8" r="7" fill="#231f20"/><path d="M1 8h14M8 1c-3 3.5-3 10.5 0 14M8 1c3 3.5 3 10.5 0 14" fill="none" stroke="#fff" stroke-width="1"/></svg>
        <span>www.harcourtmemorials.com.au</span>
      </li>
    </ul>
  </div>

  <div class="footer-band footer-band--left"></div>
  <div class="footer-band footer-band--mid"></div>
  <div class="footer-band footer-band--right"></div>
</section>

</body>
</html>
```